KRL Stationery Design Project

Dear Designers,
We need a new stationery design for company to match our new logo.
Designers should provide a design for the following:
1. Business Card: 3.5x2 Inches.
2. Letterhead: A4 size.
3. Envelops: 25x35.5 Cm.
You can keep the Arabic name at the bottom of the logo Or you can use the separate attached Arabic Name.
Please refer to the attached logo guide for design information.
Sample Business Card information:
Name: Tarek Sowan
Position: Operation Manager
Tel: +966 920007164 Ex. 500
Fax: +966 (3)8842617
Mob: +966 (5)00263817
email: tarek@krl-example.com.sa
URL: www.krl-example.com.sa
Address:
Nakheel Heights, Suite 718
Zayed bin Omar Str.
Khobar, 31847
Saudi Arabia
Updates
Dear All,
Please note, we had uploaded our logo along with Arabic writing in Adobe illustrator format (.ai).
Regards,
Karim
Dear All,
A sample data for the business card had been added as per your request.
Regards,
Karim

```html
<!DOCTYPE html>
<html lang="en">
<head>
<meta charset="utf-8">
<title>KRL Route Logistics – Business Card</title>
<link href="https://fonts.googleapis.com/css2?family=Source+Sans+3:wght@400;600;700&display=swap" rel="stylesheet">
<style>
  :root {
    --navy: #0e2a4f;
    --grey: #9a9a9c;
    --text: #222831;
    --card: #ffffff;
    --backdrop: #e6e4e1;
  }
  * { box-sizing: border-box; margin: 0; padding: 0; }
  html, body { width: 1200px; height: 472px; overflow: hidden; }
  body {
    background: var(--backdrop);
    font-family: "Source Sans 3", "Myriad Pro", Arial, sans-serif;
    color: var(--text);
    position: relative;
  }
  .card {
    position: absolute;
    top: 84px;
    width: 525px;
    height: 299px;
    background: var(--card);
    border-radius: 12px;
    overflow: hidden;
    box-shadow: 0 2px 6px rgba(0,0,0,.18);
  }
  .card--front { left: 50px; }
  .card--back { left: 612px; }

  .card__band {
    position: absolute;
    left: 0; right: 0; bottom: 0;
    height: 38px;
    background: var(--navy);
    color: #fff;
    font-size: 13px;
    display: flex;
    align-items: center;
    justify-content: center;
    border-top: 4px solid #fff;
    box-shadow: 0 -2px 0 var(--grey);
  }
  .card--back .card__band { letter-spacing: 1px; }

  .brand {
    position: absolute;
    display: flex;
    align-items: center;
    gap: 12px;
    color: var(--navy);
    font-weight: 700;
    white-space: nowrap;
  }
  .brand__dot {
    width: 22px; height: 22px;
    border-radius: 50%;
    background: var(--navy);
    flex: none;
  }
  .card--front .brand { left: 42px; top: 70px; font-size: 38px; }
  .card--back .brand { left: 108px; top: 106px; font-size: 34px; }

  .contact {
    position: absolute;
    left: 0; top: 204px;
    width: 100%;
    height: 48px;
  }
  .contact__person {
    position: absolute;
    right: 348px; top: 14px;
    font-size: 17px;
    font-weight: 700;
    color: var(--navy);
    white-space: nowrap;
  }
  .contact__person span { font-weight: 400; font-size: 13px; color: var(--text); }
  .contact__arrow { position: absolute; left: 183px; top: 2px; }
  .contact__list {
    position: absolute;
    top: 4px;
    list-style: none;
    font-size: 13px;
    line-height: 18px;
  }
  .contact__list li { display: flex; align-items: center; gap: 6px; }
  .contact__list svg { flex: none; }
  .contact__list--phones { left: 214px; }
  .contact__list--web { left: 337px; }
  .contact__divider {
    position: absolute;
    left: 326px; top: 6px;
    width: 1px; height: 32px;
    background: var(--grey);
  }
</style>
</head>
<body>
  <section class="card card--front">
    <div class="brand"><span class="brand__dot"></span>KRL Route Logistics</div>

    <div class="contact">
      <p class="contact__person">YOUR NAME, <span>Title</span></p>
      <svg class="contact__arrow" width="12" height="44" viewBox="0 0 12 44" aria-hidden="true">
        <polygon points="0,0 12,22 0,44" fill="var(--grey)"/>
      </svg>
      <ul class="contact__list contact__list--phones">
        <li>
          <svg width="11" height="11" viewBox="0 0 12 12" aria-hidden="true"><circle cx="6" cy="6" r="5.3" fill="none" stroke="var(--navy)" stroke-width="1.2"/><path d="M4 3.2l1.2 1.4-.6.8c.4.8 1 1.4 1.8 1.8l.8-.6L8.6 8l-.6 1C5.6 8.8 3.4 6.6 3.2 4.2z" fill="var(--navy)"/></svg>
          123-456-7890
        </li>
        <li>
          <svg width="11" height="11" viewBox="0 0 12 12" aria-hidden="true"><path d="M2 6l1.4-3.4h5.2L10 6v4H8.6V9H3.4v1H2z" fill="var(--navy)"/></svg>
          123-456-7890
        </li>
      </ul>
      <span class="contact__divider"></span>
      <ul class="contact__list contact__list--web">
        <li>
          <svg width="11" height="11" viewBox="0 0 12 12" aria-hidden="true"><rect x="1" y="3" width="10" height="7" rx="1" fill="var(--navy)"/><path d="M1.5 3.5L6 7l4.5-3.5" stroke="#fff" fill="none"/></svg>
          info@krl-example.com.sa
        </li>
        <li>
          <svg width="11" height="11" viewBox="0 0 12 12" aria-hidden="true"><circle cx="6" cy="6" r="5.3" fill="var(--navy)"/><path d="M1 6h10M6 1v10" stroke="#fff" stroke-width=".8"/></svg>
          www.website.com
        </li>
      </ul>
    </div>

    <div class="card__band">Street Name, City Name State, City Zip 123 4560</div>
  </section>

  <section class="card card--back">
    <div class="brand"><span class="brand__dot"></span>KRL Route Logistics</div>
    <div class="card__band">www.website.com</div>
  </section>
</body>
</html>
```